Create a business promotion flyer to leave in customer mailboxes. We are a bulk petroleum supplier, servicing any industry that requires diesel. Base in griffith NSW, servicing griffith area and surrounds.

Business Name - Terra Diesel
Fuel@terradiesel-example.com.au
Owen - 0491 570 362 ohartley@terradiesel-example.com.au
Liam - 0491 570 718 lprosser@terradiesel-example.com.au
Simon - 0491 570 905 skenway@terradiesel-example.com.au
Office 02 5550 1734

Bulk Fuel deliveries.
Oils & lubricants
Local Family owned business

```html
<!DOCTYPE html>
<html lang="en">
<head>
<meta charset="utf-8">
<title>Terra Diesel – Bulk Fuel Deliveries Flyer</title>
<link rel="stylesheet" href="https://fonts.googleapis.com/css2?family=Bebas+Neue&family=Oswald:wght@500;600&family=Poppins:ital,wght@0,400;0,600;0,700;1,700&display=swap">
<style>
  :root {
    --red: #e8322a;
    --grey: #666768;
    --grey-dark: #4f5052;
    --ink: #3a3b3d;
    --white: #ffffff;
    --map: #e6e3e3;
    --stage: #222222;
  }
  * { box-sizing: border-box; margin: 0; padding: 0; }
  html, body { width: 980px; height: 1200px; overflow: hidden; background: var(--stage); }
  .flyer {
    position: absolute; left: 30px; top: 5px; width: 920px; height: 1190px;
    overflow: hidden; background: var(--grey); font-family: "Poppins", sans-serif; color: var(--white);
  }
  .hero-photo {
    position: absolute; left: 0; top: 0; width: 920px; height: 720px;
    background: linear-gradient(180deg, #2f6db8 0%, #6f9fd6 22%, #c9ccd2 40%, #eef0f1 52%, #9ea2a7 62%, #cfcfcc 78%, #d8d6d2 100%);
  }
  .shapes { position: absolute; left: 0; top: 0; }
  .brand-box {
    position: absolute; left: 41px; top: 0; width: 241px; height: 243px; background: var(--white);
    display: flex; align-items: center; justify-content: center;
  }
  .brand-name { font-family: "Poppins", sans-serif; font-weight: 600; font-size: 34px; color: var(--red); line-height: 1.05; text-align: center; }
  .headline {
    position: absolute; left: 333px; top: 30px; width: 545px;
    font-family: "Bebas Neue", sans-serif; font-size: 72px; line-height: 1; letter-spacing: 0.5px; white-space: nowrap;
  }
  .tagline {
    position: absolute; left: 329px; top: 104px; width: 450px; height: 36px; background: var(--red);
    transform: skewX(-8deg); display: flex; align-items: center; justify-content: center;
  }
  .tagline span { transform: skewX(8deg); font-weight: 700; font-style: italic; font-size: 19px; letter-spacing: 0.2px; }
  .base-map { position: absolute; left: 56px; top: 391px; }
  .base-text { position: absolute; left: 60px; top: 460px; width: 340px; text-align: center; font-family: "Oswald", sans-serif; font-weight: 600; line-height: 1; }
  .base-text .pre { color: var(--red); font-size: 38px; }
  .base-text .town { color: var(--red); font-size: 64px; margin-top: 4px; letter-spacing: 1px; }
  .base-text .state { color: var(--ink); font-size: 48px; }
  .service-band {
    position: absolute; left: 0; top: 694px; width: 470px; height: 115px; background: var(--red);
    border-radius: 0 58px 58px 0;
  }
  .service-text {
    position: absolute; left: 66px; top: 711px; font-family: "Oswald", sans-serif; font-weight: 600;
    font-size: 30px; line-height: 1.2; letter-spacing: 0.6px;
  }
  .service-icon {
    position: absolute; left: 364px; top: 706px; width: 92px; height: 92px; border-radius: 50%;
    background: #ecebeb; display: flex; align-items: center; justify-content: center;
  }
  .contact-box {
    position: absolute; left: 63px; top: 853px; width: 400px; height: 158px;
    border: 1.5px solid #d5d5d5; border-radius: 16px;
  }
  .contact-title {
    position: absolute; left: 75px; top: 835px; padding: 0 8px; background: var(--grey);
    font-family: "Oswald", sans-serif; font-weight: 500; font-size: 26px; line-height: 1.3; letter-spacing: 0.5px;
  }
  .contact-list { position: absolute; left: 96px; top: 878px; list-style: none; }
  .contact-list li { display: flex; align-items: center; height: 37px; }
  .contact-list .name { width: 125px; font-size: 23px; margin-left: 10px; }
  .contact-list .phone { font-size: 23px; font-weight: 600; margin-left: 8px; letter-spacing: 0.3px; }
  .email { position: absolute; left: 90px; top: 1022px; display: flex; align-items: center; font-size: 23px; }
  .email svg { margin-right: 12px; }
  .services-title { position: absolute; left: 555px; top: 600px; font-family: "Oswald", sans-serif; font-weight: 600; line-height: 1; }
  .services-title .small { font-size: 38px; display: block; letter-spacing: 0.5px; }
  .services-title .big { font-size: 60px; display: block; margin-top: 2px; letter-spacing: 0.5px; }
  .services-rule { position: absolute; left: 555px; top: 717px; width: 73px; height: 4px; background: var(--red); }
  .feature { position: absolute; left: 541px; display: flex; align-items: center; }
  .feature .icon {
    width: 100px; height: 100px; border-radius: 50%; background: #ecebeb; border: 5px solid #8a8b8c;
    box-shadow: 0 0 0 2px #e9e9e9; display: flex; align-items: center; justify-content: center;
  }
  .feature p { margin-left: 18px; font-size: 23px; line-height: 1.22; }
  .feature-1 { top: 736px; } .feature-2 { top: 854px; } .feature-3 { top: 970px; }
  .footer {
    position: absolute; left: 0; top: 1115px; width: 920px; height: 75px; background: var(--white);
    display: flex; align-items: center; justify-content: center;
    font-family: "Bebas Neue", sans-serif; font-style: italic; font-size: 34px; letter-spacing: 4px; white-space: nowrap;
  }
  .footer .lead { color: var(--red); }
  .footer .close { color: var(--ink); margin-left: 14px; }
</style>
</head>
<body>
<main class="flyer">
  <div class="hero-photo" role="img" aria-label="Photo of a white road train fuel tanker with two trailers parked outside a large steel shed under a blue cloudy sky"></div>

  <svg class="shapes" width="920" height="1190" viewBox="0 0 920 1190" aria-hidden="true">
    <path d="M0,694 C260,560 560,462 920,462 L920,1190 L0,1190 Z" fill="var(--red)"/>
    <path d="M0,720 C260,600 560,545 920,541 L920,1190 L0,1190 Z" fill="var(--grey)"/>
    <path d="M460,1115 L920,760 L920,1115 Z M0,900 L300,1115 L0,1115 Z" fill="var(--grey-dark)" opacity="0.18"/>
  </svg>

  <div class="brand-box"><span class="brand-name">Terra<br>Diesel</span></div>

  <h1 class="headline">FUEILLING YOUR INDUSTRY</h1>
  <div class="tagline"><span>RELIABLE. LOCAL. READY TO DELIVER</span></div>

  <svg class="base-map" width="346" height="303" viewBox="0 0 346 303" aria-hidden="true">
    <defs><clipPath id="disc-clip"><rect x="0" y="0" width="346" height="303"/></clipPath></defs>
    <g clip-path="url(#disc-clip)">
      <circle cx="173" cy="173" r="173" fill="var(--red)"/>
      <circle cx="173" cy="173" r="166" fill="var(--grey)"/>
      <circle cx="173" cy="173" r="158" fill="var(--map)" role="img" aria-label="Map of southern New South Wales around Griffith"/>
    </g>
  </svg>
  <div class="base-text">
    <div class="pre">BASED IN</div>
    <div class="town">GRIFFITH</div>
    <div class="state">NSW</div>
  </div>
  <svg style="position:absolute;left:208px;top:620px" width="44" height="60" viewBox="0 0 44 60" aria-hidden="true">
    <path d="M22,2 C11,2 2,11 2,22 C2,36 22,58 22,58 C22,58 42,36 42,22 C42,11 33,2 22,2 Z" fill="var(--red)"/>
    <circle cx="22" cy="22" r="9" fill="var(--map)"/>
  </svg>

  <div class="service-band"></div>
  <div class="service-text">SERVICING GRIFFITH<br>AREA &amp; SURROUNDS</div>
  <div class="service-icon">
    <svg width="74" height="42" viewBox="0 0 74 42" aria-hidden="true" fill="none" stroke="#222" stroke-width="2.5" stroke-linejoin="round">
      <rect x="2" y="2" width="50" height="28"/>
      <path d="M52,10 H63 L71,20 V30 H52 Z"/><path d="M56,13 H62 L67,20 H56 Z"/>
      <line x1="2" y1="34" x2="71" y2="34"/>
      <circle cx="12" cy="36" r="4" fill="#ecebeb"/><circle cx="22" cy="36" r="4" fill="#ecebeb"/><circle cx="61" cy="36" r="4" fill="#ecebeb"/>
    </svg>
  </div>

  <div class="contact-box"></div>
  <h2 class="contact-title">CONTACT OUR TEAM</h2>
  <ul class="contact-list">
    <li>
      <svg width="22" height="22" viewBox="0 0 22 22" fill="none" stroke="#ddd" stroke-width="2"><rect x="1.5" y="3" width="17" height="17" rx="2"/><path d="M6,11 L10,15 L20,3"/></svg>
      <span class="name">Owen</span>
      <svg width="28" height="28" viewBox="0 0 28 28"><circle cx="14" cy="14" r="14" fill="var(--red)"/><path d="M9,7 L12,10 L10.5,12.5 C11.5,15 13,16.5 15.5,17.5 L18,16 L21,19 L19,21.5 C13,21 7,15 6.5,9 Z" fill="none" stroke="#fff" stroke-width="1.6"/></svg>
      <span class="phone">0491 570 362</span>
    </li>
    <li>
      <svg width="22" height="22" viewBox="0 0 22 22" fill="none" stroke="#ddd" stroke-width="2"><rect x="1.5" y="3" width="17" height="17" rx="2"/><path d="M6,11 L10,15 L20,3"/></svg>
      <span class="name">Liam</span>
      <svg width="28" height="28" viewBox="0 0 28 28"><circle cx="14" cy="14" r="14" fill="var(--red)"/><path d="M9,7 L12,10 L10.5,12.5 C11.5,15 13,16.5 15.5,17.5 L18,16 L21,19 L19,21.5 C13,21 7,15 6.5,9 Z" fill="none" stroke="#fff" stroke-width="1.6"/></svg>
      <span class="phone">0491 570 718</span>
    </li>
    <li>
      <svg width="22" height="22" viewBox="0 0 22 22" fill="none" stroke="#ddd" stroke-width="2"><rect x="1.5" y="3" width="17" height="17" rx="2"/><path d="M6,11 L10,15 L20,3"/></svg>
      <span class="name">Simon</span>
      <svg width="28" height="28" viewBox="0 0 28 28"><circle cx="14" cy="14" r="14" fill="var(--red)"/><path d="M9,7 L12,10 L10.5,12.5 C11.5,15 13,16.5 15.5,17.5 L18,16 L21,19 L19,21.5 C13,21 7,15 6.5,9 Z" fill="none" stroke="#fff" stroke-width="1.6"/></svg>
      <span class="phone">0491 570 905</span>
    </li>
  </ul>
  <p class="email">
    <svg width="32" height="24" viewBox="0 0 32 24" fill="none" stroke="#ddd" stroke-width="1.8"><rect x="1" y="1" width="30" height="22"/><path d="M1,1 L16,14 L31,1 M1,23 L12,11 M31,23 L20,11"/></svg>
    Fuel@terradiesel-example.com.au
  </p>

  <h2 class="services-title"><span class="small">BULK FUEL</span><span class="big">DELIVERIES</span></h2>
  <div class="services-rule"></div>

  <svg class="shapes" width="920" height="1190" viewBox="0 0 920 1190" aria-hidden="true">
    <path d="M660,844 H840 L856,826" fill="none" stroke="#d8d8d8" stroke-width="1.5"/>
    <circle cx="858" cy="823" r="4" fill="var(--red)"/>
    <path d="M660,963 H840 L856,945" fill="none" stroke="#d8d8d8" stroke-width="1.5"/>
    <circle cx="858" cy="942" r="4" fill="var(--red)"/>
  </svg>

  <div class="feature feature-1">
    <div class="icon">
      <svg width="56" height="56" viewBox="0 0 56 56" fill="none" stroke="#444" stroke-width="2" stroke-linejoin="round">
        <path d="M18,46 L8,52 M20,44 L30,22 L40,18 L44,24 L36,34 L26,48 Z"/><path d="M30,22 L36,10 L42,14 L40,18"/>
        <path d="M48,28 C48,28 44,33 44,35 C44,37 46,38 48,38 C50,38 52,37 52,35 C52,33 48,28 48,28 Z" stroke="var(--red)"/>
      </svg>
    </div>
    <p>Oils &amp;<br>lubricants</p>
  </div>
  <div class="feature feature-2">
    <div class="icon">
      <svg width="62" height="46" viewBox="0 0 62 46" fill="none" stroke="var(--red)" stroke-width="2" stroke-linejoin="round">
        <rect x="4" y="6" width="34" height="22" rx="6"/><path d="M21,11 L26,17 L21,23 L16,17 Z"/>
        <g stroke="#444"><path d="M38,14 H48 L56,24 V34 H2 V28"/><circle cx="10" cy="38" r="4"/><circle cx="20" cy="38" r="4"/><circle cx="48" cy="38" r="4"/></g>
      </svg>
    </div>
    <p>Petrol<br>deliverie</p>
  </div>
  <div class="feature feature-3">
    <div class="icon">
      <svg width="70" height="70" viewBox="0 0 70 70" fill="none" aria-hidden="true">
        <circle cx="35" cy="35" r="31" stroke="#444" stroke-width="1.5"/>
        <circle cx="35" cy="35" r="14" fill="var(--red)"/>
      </svg>
    </div>
    <p>Local Family<br>owned business</p>
  </div>

  <footer class="footer"><span class="lead">FUEILLING YOUR BUSINESS.</span><span class="close">FUELLING OUR COMMUNITY</span></footer>
</main>
</body>
</html>
```